Investment Advisor E-Newsletter Banner Design

I need a banner designed for an email newsletter that will be sent monthly to clients and prospects. We want to see designs that are elegant and use our logo well. The banner should be 922x150px and should go well with the www.tlvbanda.com website. Should include Logo and email and phone number.

Target Market(s)

High net worth investors

Number of Pages Required

1 page

Requirements
Must have
• logo, place for email (info@tlvbanda.com) and phone number (415-297-6180), colors and design that work well with www.tlvbanda.com website

```html
<!DOCTYPE html>
<html lang="en">
<head>
<meta charset="UTF-8">
<title>Harbor Lane Capital – Newsletter Banner</title>
<link rel="stylesheet" href="https://fonts.googleapis.com/css2?family=Montserrat:wght@500;700&family=Open+Sans:wght@600&display=swap">
<style>
  :root {
    --page-bg: #e9eaec;
    --banner-bg: #eef0f4;
    --banner-edge: #e2e5ea;
    --ink: #2a2a2a;
    --brand-blue: #1414a0;
    --button-blue: #0808a0;
    --white: #ffffff;
  }
  * { margin: 0; padding: 0; box-sizing: border-box; }
  html, body {
    width: 1200px;
    height: 1200px;
    overflow: hidden;
    background: var(--page-bg);
  }
  .canvas {
    width: 1200px;
    height: 1200px;
    display: flex;
    align-items: center;
    justify-content: center;
  }
  .banner {
    width: 1106px;
    height: 180px;
    background: linear-gradient(180deg, var(--banner-bg), var(--banner-edge));
    display: flex;
    align-items: stretch;
    box-shadow: 0 10px 24px rgba(0,0,0,0.12);
  }
  .banner__pitch {
    width: 350px;
    display: flex;
    flex-direction: column;
    align-items: center;
    justify-content: center;
    gap: 20px;
  }
  .banner__headline {
    font-family: "Montserrat", sans-serif;
    font-weight: 700;
    font-size: 20px;
    line-height: 1.18;
    letter-spacing: 0.3px;
    color: var(--ink);
    text-align: center;
    text-transform: uppercase;
  }
  .banner__button {
    font-family: "Open Sans", sans-serif;
    font-weight: 600;
    font-size: 15px;
    color: var(--white);
    background: var(--button-blue);
    padding: 8px 19px;
    border-radius: 3px;
    text-decoration: none;
  }
  .banner__photo {
    width: 426px;
    background: linear-gradient(90deg, #c9ccd3 0%, #3a4766 18%, #1d2233 38%, #2a2c3a 60%, #27314f 82%, #cfd2d8 100%);
  }
  .banner__brand {
    flex: 1;
    display: flex;
    flex-direction: column;
    align-items: center;
    justify-content: center;
    gap: 22px;
  }
  .brand {
    display: flex;
    align-items: center;
    gap: 12px;
  }
  .brand__dot {
    width: 44px;
    height: 44px;
    border-radius: 50%;
    background: var(--brand-blue);
    flex: none;
  }
  .brand__name {
    font-family: "Montserrat", sans-serif;
    font-weight: 500;
    color: var(--brand-blue);
    font-size: 22px;
    line-height: 1.15;
  }
  .brand__name small {
    display: block;
    font-size: 12px;
  }
  .banner__contact {
    font-family: "Montserrat", sans-serif;
    font-weight: 500;
    font-size: 16px;
    color: #111;
  }
</style>
</head>
<body>
  <main class="canvas">
    <section class="banner">
      <div class="banner__pitch">
        <h1 class="banner__headline">Evidence-Based<br>Investment Management.<br>Personal Service.</h1>
        <a class="banner__button" href="#">Learn More</a>
      </div>
      <div class="banner__photo" role="img" aria-label="Group photo of four advisors in suits, one holding an award"></div>
      <div class="banner__brand">
        <div class="brand">
          <span class="brand__dot"></span>
          <p class="brand__name">Harbor Lane Capital<small>Management &amp; Research, Inc.</small></p>
        </div>
        <p class="banner__contact">415-297-6180 / info@tlvbanda.com</p>
      </div>
    </section>
  </main>
</body>
</html>
```